e-commerce store for sport clothing online store "baseball merchandise "web application...

I want to design a UX/UI for my web application website for the online store I will provide you with the following:
1. screen shots of the initial design for the pages>
2. the logo files.
3. The brand guideline file.

the provided files (screen shots) is guideline I want to see CREATIVITY with the UX/UI DESIGN.
PS. PLEASE FOLLOW THE BRANDGUIDE LINE CAREFULLY SPECIALLY THE TYPOGRAPHY & THE COLOR CODES.

PLEASE VISIT THIS WEBSITE brightlane.varomi-qz.com to see more for the screens.

```html
<!DOCTYPE html>
<html lang="en">
<head>
<meta charset="utf-8">
<title>Fieldhouse Store – Cart &amp; Checkout</title>
<link href="https://fonts.googleapis.com/css2?family=Lato:wght@400;700;900&family=Libre+Baskerville&display=swap" rel="stylesheet">
<style>
  :root{
    --brand-red:#ab0f31;
    --navy:#0d2147;
    --ink:#1b1b1b;
    --muted:#6d6d6d;
    --line:#cfcfcf;
    --stage:#e7e7e7;
    --white:#ffffff;
  }
  *{box-sizing:border-box;margin:0;padding:0}
  html,body{width:1045px;height:1200px;overflow:hidden;background:var(--white);font-family:'Lato',sans-serif;color:var(--ink)}
  .stage{position:absolute;left:32px;width:979px;height:559px;background:var(--stage)}
  .stage--cart{top:24px}
  .stage--checkout{top:605px}
  .app{position:absolute;left:32px;top:27px;width:916px;height:506px;background:var(--white);border-radius:28px;overflow:hidden}
  .stage--checkout .app{top:26px}

  .sidebar{position:absolute;left:0;top:0;width:158px;height:100%;background:var(--brand-red);color:var(--white)}
  .brand{position:absolute;left:0;top:36px;width:158px;text-align:center}
  .brand__dot{display:block;width:22px;height:22px;border-radius:50%;background:var(--white);margin:0 auto 8px}
  .brand__name{font-weight:900;font-size:21px;letter-spacing:.5px;color:var(--white)}
  .menu{position:absolute;left:0;top:120px;width:158px;list-style:none}
  .menu__item{position:relative;height:33px;display:flex;align-items:center;padding-left:47px;font-size:13px}
  .menu__item svg{position:absolute;left:17px;top:50%;transform:translateY(-50%);width:13px;height:13px}
  .menu__item--active{background:var(--white);color:var(--brand-red);margin-left:10px;padding-left:37px;border-radius:18px 0 0 18px;height:36px;margin-top:-1px;margin-bottom:-2px}
  .menu__item--active svg{left:7px}
  .social{position:absolute;left:15px;top:474px;width:130px;display:flex;justify-content:space-between;font-family:'Libre Baskerville',serif;font-size:8.5px;white-space:nowrap}
  .social a{color:var(--white);text-decoration:underline}

  .topbar{position:absolute;left:158px;top:0;right:0;height:44px;background:var(--white);box-shadow:0 3px 5px rgba(0,0,0,.07)}
  .nav{position:absolute;top:0;height:44px;display:flex;align-items:center;font-size:13px}
  .nav a{position:absolute;white-space:nowrap;color:var(--ink);text-decoration:none}
  .search{position:absolute;left:341px;top:9px;width:277px;height:25px;border:1px solid #bdbdbd;border-radius:13px;background:#ececec;font-size:8px;color:#444;padding:7px 8px}
  .search svg{position:absolute;right:9px;top:6px;width:11px;height:11px}
  .bell{position:absolute;left:640px;top:14px;width:15px;height:16px}
  .bell__badge{position:absolute;left:651px;top:11px;width:8px;height:8px;border-radius:50%;background:#d9152f;color:var(--white);font-size:5px;text-align:center;line-height:8px}
  .divider{position:absolute;left:672px;top:12px;width:1px;height:20px;background:#ddd}
  .avatar{position:absolute;left:682px;top:8px;width:28px;height:28px;border-radius:50%;background:radial-gradient(circle at 50% 40%,#f0d3c2 0 30%,#3b6fc4 31% 100%);border:2px solid #f3e7e2}
  .caret{position:absolute;left:724px;top:19px;width:8px;height:6px}

  .main{position:absolute;left:0;top:0;width:100%;height:100%}
  .heading{position:absolute;font-weight:700;color:var(--navy);font-size:14px}
  .view-all{position:absolute;font-size:12px;color:#8a8a8a;text-align:right}

  .hero{position:absolute;left:175px;top:63px;width:501px;height:155px;border-radius:22px;background:linear-gradient(100deg,#5a3a2a 0%,#c45a3c 25%,#e9e6e1 42%,#1a1c2a 55%,#d7d4cf 68%,#b37ac9 82%,#4fb5a5 100%)}
  .product{position:absolute;top:268px;width:119px}
  .product__img{height:139px;border-radius:12px;background:linear-gradient(180deg,#e6b9c6 0%,#c9c3d2 70%,#b9bccc 100%)}
  .product__name{margin-top:10px;padding-left:6px;font-size:12px;line-height:16px;font-weight:500}
  .product__desc{margin-top:4px;padding-left:6px;font-size:9.5px;line-height:14px;color:#4a4a4a}
  .product__price{position:absolute;top:209px;left:6px;font-size:13px;font-weight:700;color:var(--brand-red)}

  .line-item{position:absolute;width:199px;height:65px;border:1px solid var(--line);border-radius:11px;background:var(--white)}
  .line-item__img{position:absolute;left:5px;top:6px;width:46px;height:52px;border-radius:6px}
  .img--trunks{background:linear-gradient(160deg,#c9d9ea,#9ab4d4 60%,#e1c2c6)}
  .img--cap{background:linear-gradient(160deg,#eef0f3,#a7acb4 60%,#d6d9de)}
  .line-item__name{position:absolute;left:57px;top:13px;font-size:11px;white-space:nowrap}
  .line-item__price{position:absolute;left:57px;top:36px;font-size:13px;font-weight:700;color:var(--brand-red)}
  .stepper{position:absolute;right:7px;top:38px;width:44px;height:16px;border:1px solid #9a9a9a;border-radius:8px;display:flex;justify-content:space-around;align-items:center;font-size:11px;font-weight:700}
  .stepper b{font-size:13px}
  .dashed{position:absolute;height:0;border-top:1px dashed #b8b8b8}

  .summary-row{position:absolute;left:697px;width:191px;display:flex;justify-content:space-between;font-size:12px;color:#2a2a2a}
  .summary-row--total{font-weight:700;font-size:15px;color:var(--navy)}
  .summary-row--total span:last-child{font-size:12px;color:var(--ink)}
  .btn-primary{position:absolute;background:var(--navy);color:var(--white);border-radius:22px;font-weight:900;display:flex;align-items:center;justify-content:center}

  .field{position:absolute;height:34px;border:1px solid var(--line);border-radius:5px;font-size:10px;color:#555;padding:11px 10px}
  .label{position:absolute;font-weight:700;font-size:13px;color:#3a3a3a}
  .pay-option{position:absolute;left:460px;top:402px;font-size:12px;color:#333;display:flex;align-items:center;gap:12px}
  .coupon{position:absolute;left:457px;top:457px;width:230px;height:34px;border:1px solid var(--line);border-radius:5px;font-size:12px;color:#666;padding:9px 8px}
  .coupon__apply{position:absolute;right:4px;top:3px;width:62px;height:27px;border-radius:5px;background:var(--brand-red);color:var(--white);font-weight:700;font-size:13px;text-align:center;line-height:27px}
  .bill-row{position:absolute;left:709px;width:192px;display:flex;justify-content:space-between;font-size:11.5px}
  .bill-qty{position:absolute;left:709px;font-size:13px;font-weight:700;color:var(--brand-red)}
  .bill-row--total{font-size:14px;font-weight:700}
  .bill-row--total span:last-child{font-size:11.5px;font-weight:400}
</style>
</head>
<body>

<section class="stage stage--cart">
  <div class="app">
    <aside class="sidebar">
      <div class="brand"><span class="brand__dot"></span><span class="brand__name">Fieldhouse</span></div>
      <ul class="menu">
        <li class="menu__item"><svg viewBox="0 0 16 16"><path d="M8 1 0 8h2v7h4v-5h4v5h4V8h2z" fill="#fff"/></svg>Home</li>
        <li class="menu__item"><svg viewBox="0 0 16 16"><path d="M0 2h3l1 2h12l-2 6H5l-1 2h10v1H3l2-3L2 3H0z" fill="#fff"/><circle cx="5" cy="15" r="1" fill="#fff"/><circle cx="13" cy="15" r="1" fill="#fff"/></svg>My Cart</li>
        <li class="menu__item menu__item--active"><svg viewBox="0 0 16 16"><circle cx="8" cy="8" r="6.5" fill="none" stroke="#ab0f31" stroke-width="2"/><path d="M8 4v4H5" fill="none" stroke="#ab0f31" stroke-width="2"/></svg>Track Order</li>
        <li class="menu__item"><svg viewBox="0 0 16 16"><circle cx="8" cy="8" r="8" fill="#fff"/><path d="M5.8 6a2.2 2.2 0 1 1 3 2c-.6.3-.8.7-.8 1.4" fill="none" stroke="#ab0f31" stroke-width="1.8"/><circle cx="8" cy="12" r="1" fill="#ab0f31"/></svg>Contact</li>
      </ul>
      <nav class="social"><a>Friendbook</a><a>Chirper</a><a>Seeker</a></nav>
    </aside>

    <header class="topbar">
      <nav class="nav"><a style="left:24px">Men</a><a style="left:83px">Woman</a><a style="left:161px">Sports Kit</a><a style="left:252px">Baseball</a></nav>
      <div class="search">Search<svg viewBox="0 0 12 12"><circle cx="5" cy="5" r="3.8" fill="none" stroke="#222" stroke-width="1.6"/><path d="M8 8l3 3" stroke="#222" stroke-width="1.6"/></svg></div>
      <svg class="bell" viewBox="0 0 16 16"><path d="M8 1a5 5 0 0 0-5 5v4l-2 3h14l-2-3V6a5 5 0 0 0-5-5z" fill="#2b5fd0"/><circle cx="8" cy="15" r="1.5" fill="#2b5fd0"/></svg>
      <span class="bell__badge">3</span>
      <span class="divider"></span>
      <span class="avatar" role="img" aria-label="Customer profile photo"></span>
      <svg class="caret" viewBox="0 0 8 6"><path d="M0 0h8L4 5z" fill="#333"/></svg>
    </header>

    <div class="main">
      <div class="hero" role="img" aria-label="Photo of trucker caps lined up beside folded colourful shirts"></div>

      <h2 class="heading" style="left:177px;top:242px">Mako Reef</h2>
      <span class="view-all" style="left:620px;top:243px;width:53px">View All</span>

      <article class="product" style="left:176px"><div class="product__img" role="img" aria-label="Black graphic surf tee"></div><h3 class="product__name">Palm Surf Pals</h3><p class="product__desc">Turn heads in the Palm Surf Pals Tee</p><span class="product__price">19.00 KD</span></article>
      <article class="product" style="left:303px"><div class="product__img" role="img" aria-label="Blue patterned boonie hat with chin strap"></div><h3 class="product__name">Scuba Boonie Hat</h3><p class="product__desc">The Scuba Boonie hat can Handle</p><span class="product__price">20.00 KD</span></article>
      <article class="product" style="left:430px"><div class="product__img" role="img" aria-label="Model wearing a mint green graphic tee"></div><h3 class="product__name">Hit The beach Graphic Tee</h3><p class="product__desc">The Name says it all!</p><span class="product__price">19.00 KD</span></article>
      <article class="product" style="left:556px"><div class="product__img" role="img" aria-label="Black boonie hat with patch"></div><h3 class="product__name">Mako Reef Patch Logo Boonie hat</h3><p class="product__desc">The Mako Reef Patch</p><span class="product__price">20.00 KD</span></article>

      <h2 class="heading" style="left:693px;top:67px">Order List</h2>
      <span class="view-all" style="left:830px;top:67px;width:64px">View All</span>

      <div class="line-item" style="left:694px;top:103px"><span class="line-item__img img--trunks" role="img" aria-label="Kids swim trunks"></span><span class="line-item__name">Splashy kids Swim Trunks</span><span class="line-item__price">23.00 KD</span><span class="stepper">-<b>2</b>+</span></div>
      <div class="line-item" style="left:694px;top:177px"><span class="line-item__img img--cap" role="img" aria-label="Grey trucker cap"></span><span class="line-item__name">Bass trucker Cap</span><span class="line-item__price">13.00 KD</span><span class="stepper">-<b>1</b>+</span></div>

      <span class="dashed" style="left:699px;top:272px;width:189px"></span>
      <h2 class="heading" style="left:697px;top:288px">Summary</h2>
      <div class="summary-row" style="top:323px"><span>Subtotal</span><span>$13.00</span></div>
      <div class="summary-row" style="top:351px"><span>Eastimsted Delivery</span><span>$0.00</span></div>
      <div class="summary-row" style="top:381px"><span>Estmated Duties and taxes</span><span>-</span></div>
      <div class="summary-row summary-row--total" style="top:409px;left:699px;width:190px"><span>Total</span><span>$13.00</span></div>
      <div class="btn-primary" style="left:697px;top:443px;width:191px;height:41px;font-size:17px">Check out</div>
    </div>
  </div>
</section>

<section class="stage stage--checkout">
  <div class="app">
    <aside class="sidebar">
      <div class="brand"><span class="brand__dot"></span><span class="brand__name">Fieldhouse</span></div>
      <ul class="menu">
        <li class="menu__item"><svg viewBox="0 0 16 16"><path d="M8 1 0 8h2v7h4v-5h4v5h4V8h2z" fill="#fff"/></svg>Home</li>
        <li class="menu__item"><svg viewBox="0 0 16 16"><path d="M0 2h3l1 2h12l-2 6H5l-1 2h10v1H3l2-3L2 3H0z" fill="#fff"/><circle cx="5" cy="15" r="1" fill="#fff"/><circle cx="13" cy="15" r="1" fill="#fff"/></svg>My Cart</li>
        <li class="menu__item menu__item--active"><svg viewBox="0 0 16 16"><circle cx="8" cy="8" r="6.5" fill="none" stroke="#ab0f31" stroke-width="2"/><path d="M8 4v4H5" fill="none" stroke="#ab0f31" stroke-width="2"/></svg>Track Order</li>
        <li class="menu__item"><svg viewBox="0 0 16 16"><circle cx="8" cy="8" r="8" fill="#fff"/><path d="M5.8 6a2.2 2.2 0 1 1 3 2c-.6.3-.8.7-.8 1.4" fill="none" stroke="#ab0f31" stroke-width="1.8"/><circle cx="8" cy="12" r="1" fill="#ab0f31"/></svg>Contact</li>
      </ul>
      <nav class="social"><a>Friendbook</a><a>Chirper</a><a>Seeker</a></nav>
    </aside>

    <header class="topbar">
      <nav class="nav"><a style="left:24px">Men</a><a style="left:83px">Woman</a><a style="left:161px">Sports Kit</a><a style="left:252px">Baseball</a></nav>
      <div class="search">Search<svg viewBox="0 0 12 12"><circle cx="5" cy="5" r="3.8" fill="none" stroke="#222" stroke-width="1.6"/><path d="M8 8l3 3" stroke="#222" stroke-width="1.6"/></svg></div>
      <svg class="bell" viewBox="0 0 16 16"><path d="M8 1a5 5 0 0 0-5 5v4l-2 3h14l-2-3V6a5 5 0 0 0-5-5z" fill="#2b5fd0"/><circle cx="8" cy="15" r="1.5" fill="#2b5fd0"/></svg>
      <span class="bell__badge">3</span>
      <span class="divider"></span>
      <span class="avatar" role="img" aria-label="Customer profile photo"></span>
      <svg class="caret" viewBox="0 0 8 6"><path d="M0 0h8L4 5z" fill="#333"/></svg>
    </header>

    <div class="main">
      <svg style="position:absolute;left:183px;top:74px;width:17px;height:10px" viewBox="0 0 17 10"><path d="M1 5h16M5 1 1 5l4 4" fill="none" stroke="#0d2147" stroke-width="2"/></svg>
      <h2 class="heading" style="left:213px;top:67px;font-size:17px">Deliver To</h2>

      <div class="field" style="left:184px;top:100px;width:241px">First Name</div>
      <div class="field" style="left:446px;top:100px;width:242px">Last Name</div>
      <div class="field" style="left:184px;top:146px;width:241px">Phone Number</div>
      <div class="field" style="left:446px;top:146px;width:242px">Email Address</div>
      <div class="field" style="left:184px;top:193px;width:504px">Area *</div>
      <div class="field" style="left:183px;top:241px;width:242px">Block *</div>
      <div class="field" style="left:448px;top:241px;width:241px">Street *</div>
      <div class="field" style="left:183px;top:285px;width:242px">Avenue</div>
      <div class="field" style="left:448px;top:285px;width:241px">Building</div>
      <div class="field" style="left:183px;top:330px;width:242px">Floor</div>
      <div class="field" style="left:448px;top:330px;width:241px">Appartment</div>
      <div class="field" style="left:184px;top:374px;width:240px;height:115px">Map location</div>

      <span class="label" style="left:457px;top:374px">Payment Method</span>
      <div class="pay-option"><svg width="11" height="11" viewBox="0 0 12 12"><circle cx="6" cy="6" r="6" fill="#ab0f31"/><path d="M3 6l2 2 4-4" fill="none" stroke="#fff" stroke-width="1.6"/></svg>QuickPay Payment</div>
      <span class="label" style="left:457px;top:436px">Discount Coupon</span>
      <div class="coupon">Coupon Code<span class="coupon__apply">Apply</span></div>

      <h2 class="heading" style="left:693px;top:67px;font-size:16px">Items</h2>
      <div class="line-item" style="left:701px;top:99px"><span class="line-item__img img--trunks" role="img" aria-label="Kids swim trunks"></span><span class="line-item__name">Splashy kids Swim Trunks</span><span class="line-item__price">23.00 KD</span><span class="stepper">-<b>2</b>+</span></div>
      <div class="line-item" style="left:701px;top:173px"><span class="line-item__img img--cap" role="img" aria-label="Grey trucker cap"></span><span class="line-item__name">Bass trucker Cap</span><span class="line-item__price">13.00 KD</span><span class="stepper">-<b>1</b>+</span></div>

      <span class="dashed" style="left:706px;top:259px;width:193px"></span>
      <div class="bill-row" style="top:275px"><span>Splashy kids Swim Trunks</span><span>23.00 KD</span></div>
      <span class="bill-qty" style="top:295px">1 x 23.000 KD</span>
      <div class="bill-row" style="top:327px"><span>Bass Trucker Cap</span><span>26.00 KD</span></div>
      <span class="bill-qty" style="top:347px">2 x 13.000 KD</span>
      <div class="bill-row" style="top:378px"><span>SubTotal</span><span>49.000 KD</span></div>
      <div class="bill-row" style="top:403px"><span>Dlivery Charge</span><span>1.000 KD</span></div>
      <div class="bill-row bill-row--total" style="top:427px"><span>Total</span><span>50.000 KD</span></div>
      <div class="btn-primary" style="left:717px;top:455px;width:171px;height:37px;font-size:15px">Place Order</div>
    </div>
  </div>
</section>

</body>
</html>
```